Working Capital graphics

Our business advisory firm requires 9 images to be re-created and improved in the branding of our business.

The 9 images have been uploaded below and the colours and branding of the business can be found at the website www.tallowmereadvisory.com.au

```html
<!DOCTYPE html>
<html lang="en">
<head>
<meta charset="utf-8">
<title>Working Capital Levers Along the Value Chain</title>
<link rel="stylesheet" href="https://fonts.googleapis.com/css2?family=Jost:wght@500;600&display=swap">
<style>
  :root {
    --frame: #d6d6d6;
    --paper: #ffffff;
    --ink: #123a80;
    --navy: #0b2149;
    --royal: #10387f;
    --cobalt: #1a4fb8;
    --sky: #0db0f0;
    --orange: #fb9426;
    --apricot: #fcaa55;
    --peach: #fcc68a;
    --peach-text: #fde6c6;
    --white: #ffffff;
  }
  html, body { margin: 0; padding: 0; overflow: hidden; background: var(--paper); }
  .canvas { width: 1200px; height: 654px; overflow: hidden; }
  .chart { display: block; font-family: "Jost", "Futura", sans-serif; font-weight: 600; }
  .frame { fill: var(--paper); stroke: var(--frame); stroke-width: 20; }
  .stage-label { fill: var(--white); font-size: 27px; text-anchor: middle; dominant-baseline: central; letter-spacing: 0.5px; }
  .stage-label--light { fill: var(--peach-text); }
  .connector { fill: none; stroke: var(--ink); stroke-width: 4; }
  .lever { fill: var(--paper); stroke-width: 5; }
  .lever--payables { stroke: var(--orange); }
  .lever--receivables { stroke: var(--sky); }
  .lever-text { fill: var(--ink); font-size: 23px; text-anchor: middle; dominant-baseline: central; }
  .lever-text--small { font-size: 19px; }
  .lever-text--large { font-size: 27px; }
  .legend-text { fill: var(--ink); font-size: 19px; font-weight: 500; letter-spacing: 0.5px; dominant-baseline: central; }
</style>
</head>
<body>
<div class="canvas">
<svg class="chart" width="1200" height="654" viewBox="0 0 2393 1304" xmlns="http://www.w3.org/2000/svg">
  <rect class="frame" x="0" y="0" width="2393" height="1304"/>

  <!-- connectors -->
  <g class="connectors">
    <path class="connector" d="M234 517V600"/>
    <path class="connector" d="M700 287V333M700 517V600"/>
    <path class="connector" d="M941 517V559H459V600"/>
    <path class="connector" d="M700 830V893"/>
    <path class="connector" d="M1530 517V600"/>
    <path class="connector" d="M1908 287V333M1908 517V600M1908 830V893"/>
    <path class="connector" d="M2149 517V600M2149 830V893"/>
  </g>

  <!-- value chain -->
  <g class="value-chain">
    <polygon fill="var(--navy)" points="124,600 347,600 392,715 352,830 124,830"/>
    <polygon fill="var(--royal)" points="360,600 576,600 621,715 582,830 366,830 405,715"/>
    <polygon fill="var(--cobalt)" points="589,600 810,600 855,715 816,830 595,830 634,715"/>
    <polygon fill="var(--sky)" points="826,600 1058,600 1103,715 1064,830 832,830 871,715"/>
    <polygon fill="var(--orange)" points="1071,600 1293,600 1338,715 1299,830 1077,830 1116,715"/>
    <polygon fill="var(--apricot)" points="1304,600 1527,600 1572,715 1533,830 1310,830 1349,715"/>
    <polygon fill="var(--peach)" points="1536,600 1760,600 1805,715 1766,830 1542,830 1581,715"/>
    <polygon fill="var(--navy)" points="1768,600 1990,600 2035,715 1996,830 1774,830 1813,715"/>
    <polygon fill="var(--royal)" points="2000,600 2222,600 2267,715 2228,830 2006,830 2045,715"/>

    <text class="stage-label" x="258" y="727">DESIGN</text>
    <text class="stage-label" x="490" y="722"><tspan x="490" y="692">ORDER/</tspan><tspan x="490" y="722">MATERIAL</tspan><tspan x="490" y="752">PLANNING</tspan></text>
    <text class="stage-label" x="745" y="727">PURCHASING</text>
    <text class="stage-label" x="983" y="720">MANUFACTURING</text>
    <text class="stage-label" x="1229" y="727">PRE-ASSEMBLY</text>
    <text class="stage-label" x="1453" y="720">ASSEMBLY</text>
    <text class="stage-label stage-label--light"><tspan x="1681" y="713">PACKAGING/</tspan><tspan x="1681" y="743">SHIPPING</tspan></text>
    <text class="stage-label" x="1897" y="720">SALES</text>
    <text class="stage-label"><tspan x="2150" y="713">AFTER  SALES/</tspan><tspan x="2150" y="743">SERVICE</tspan></text>
  </g>

  <!-- levers -->
  <g class="levers">
    <circle class="lever lever--payables" cx="234" cy="425" r="92"/>
    <text class="lever-text"><tspan x="234" y="397">REDUCE PART</tspan><tspan x="234" y="423">VARIANTS/</tspan><tspan x="234" y="449">RELEASES</tspan></text>

    <circle class="lever lever--receivables" cx="700" cy="194" r="92"/>
    <text class="lever-text"><tspan x="700" y="166">MODIFY</tspan><tspan x="700" y="193">PAYMENT</tspan><tspan x="700" y="220">CONDITIONS</tspan></text>

    <circle class="lever lever--receivables" cx="700" cy="425" r="92"/>
    <text class="lever-text"><tspan x="700" y="396">OPTIMIZE</tspan><tspan x="700" y="423">PAYMENT</tspan><tspan x="700" y="451">PROCESSES</tspan></text>

    <circle class="lever lever--payables" cx="941" cy="425" r="92"/>
    <text class="lever-text lever-text--small"><tspan x="939" y="373">RETHINK</tspan><tspan x="941" y="395">DELIVERY</tspan><tspan x="939" y="417">SCHEDULES</tspan><tspan x="939" y="439">AND</tspan><tspan x="941" y="460">WAREHOUSING</tspan></text>

    <circle class="lever lever--receivables" cx="700" cy="985" r="92"/>
    <text class="lever-text"><tspan x="700" y="956">OPTIMIZE</tspan><tspan x="700" y="983">EXTERNAL</tspan><tspan x="700" y="1010">PURCHASING</tspan></text>

    <circle class="lever lever--receivables" cx="1530" cy="425" r="92"/>
    <text class="lever-text lever-text--large"><tspan x="1530" y="393">OPTIMIZE</tspan><tspan x="1530" y="423">PRODUCT</tspan><tspan x="1530" y="453">TESTING</tspan></text>

    <circle class="lever lever--receivables" cx="1908" cy="194" r="92"/>
    <text class="lever-text lever-text--large" style="font-size:25px"><tspan x="1908" y="163">IMPROVE</tspan><tspan x="1908" y="193">PAYMENT</tspan><tspan x="1908" y="223">SCHEMES</tspan></text>

    <circle class="lever lever--receivables" cx="1908" cy="425" r="92"/>
    <text class="lever-text lever-text--small"><tspan x="1908" y="399">REDUCE DUE/</tspan><tspan x="1908" y="423">OVERDUE</tspan><tspan x="1908" y="447">RECEIVABLE</tspan></text>

    <circle class="lever lever--receivables" cx="2149" cy="425" r="92"/>
    <text class="lever-text lever-text--small" style="font-size:21px"><tspan x="2149" y="401">ESTABLISH NEW</tspan><tspan x="2149" y="425">PAYMENT</tspan><tspan x="2149" y="449">CONDITIONS</tspan></text>

    <circle class="lever lever--payables" cx="1908" cy="985" r="92"/>
    <text class="lever-text lever-text--large"><tspan x="1908" y="941">REDUCE</tspan><tspan x="1908" y="972">FINISHED</tspan><tspan x="1904" y="1003">GOODS</tspan><tspan x="1908" y="1034">STOCKS</tspan></text>

    <circle class="lever lever--payables" cx="2149" cy="985" r="92"/>
    <text class="lever-text lever-text--large" style="font-size:25px"><tspan x="2146" y="970">REDUCE</tspan><tspan x="2149" y="998">INVENTORY</tspan></text>
  </g>

  <!-- legend -->
  <g class="legend">
    <g fill="none" stroke-width="5">
      <path d="M1471 1150 A16 16 0 0 1 1487 1166" stroke="var(--navy)"/>
      <path d="M1487 1166 A16 16 0 0 1 1471 1182" stroke="var(--cobalt)"/>
      <path d="M1471 1182 A16 16 0 0 1 1455 1166" stroke="var(--sky)"/>
      <path d="M1455 1166 A16 16 0 0 1 1471 1150" stroke="var(--apricot)"/>
    </g>
    <text class="legend-text" x="1500" y="1166">INVENTORY</text>

    <circle cx="1669" cy="1166" r="18" fill="none" stroke="var(--orange)" stroke-width="5"/>
    <text class="legend-text"><tspan x="1705" y="1166">PAYABLES AND</tspan><tspan x="1705" y="1190">PRE-PAYMENTS MADE</tspan></text>

    <circle cx="1970" cy="1166" r="18" fill="none" stroke="var(--sky)" stroke-width="5"/>
    <text class="legend-text"><tspan x="2006" y="1166">RECEIVABLES AND</tspan><tspan x="2006" y="1190">PRE-PAYMENTS RECEIVED</tspan></text>
  </g>
</svg>
</div>
</body>
</html>
```